Wesbite design for Investment Firm

We want a basic (clean) website that follows the form, fonts and colors of our attachments. This is for a financial investment management firm, but we have a boutique (anti-Wall Street) approach. Site should have an Home Page (Logo up top - room for basic copy on bottom, Philosophy Page (room for Quarterly Letter attachment and basic copy, Performance Page (room for Performance Overview and Performance Analysis and basic copy), Team Page, Commentary Page and Contact

Reason: Some designers have asked for an extension. Again, please only use image of Train Station or Train Station Logo in design.

Target Market(s)

Small and mid-size financial advisors from across the country

Industry/Entity Type

Financial

Number of Pages Required

5+ page

Font styles to use
Other font styles liked:
• Palotino Linotype

Colors
3176b5
cfdeed
ffffff

Requirements
Must have
• Please refer to existing site www.qlvor.example. Of note, this is too complex / cluttered. We simply want Blur, Grey and White consistent with attachments. The copy is pretty good, but will be simplified (and no quotes)
Should not have
• No images other than train station logo and / or train station image

```html
<!DOCTYPE html>
<html lang="en">
<head>
<meta charset="utf-8">
<title>Halden Row Investment Company</title>
<link rel="stylesheet" href="https://fonts.googleapis.com/css2?family=Crimson+Text&family=Open+Sans:ital,wght@0,300;0,400;0,600;1,300&display=swap">
<style>
:root{
  --blue:#3176b5;
  --blue-pale:#cfdeed;
  --white:#ffffff;
  --grey-band:#f4f4f4;
  --text:#555555;
  --text-dark:#333333;
  --rule:#e4e4e4;
  --hero-a:#6f7d8c;
  --hero-b:#c9cdd2;
  --hero-c:#3d4a3a;
}
*{box-sizing:border-box;margin:0;padding:0}
html,body{width:818px;height:1200px;overflow:hidden;background:var(--white)}
body{position:relative;font-family:"Open Sans",Arial,sans-serif;color:var(--text)}
.abs{position:absolute}

/* header */
.brand{left:0;width:818px;top:14px;text-align:center;font-family:"Crimson Text",Georgia,serif}
.brand-name{font-size:26px;color:var(--blue);line-height:30px}
.brand-tag{font-size:13px;color:#aaaaaa;line-height:14px}
.header-rule{left:68px;width:683px;top:66px;height:1px;background:var(--rule)}
.nav{left:0;width:818px;top:77px;display:flex;justify-content:center;gap:31px;font-size:10px;color:var(--text-dark);list-style:none}
.nav li.active{color:var(--blue)}

/* hero */
.hero{left:0;top:106px;width:818px;height:345px;
  background:linear-gradient(180deg,#3f78b8 0%,var(--hero-a) 22%,var(--hero-b) 55%,#9aa0a4 78%,var(--hero-c) 100%)}
.hero-shade{left:0;top:106px;width:818px;height:345px;background:rgba(0,0,0,.12)}
.hero-title{left:0;width:818px;top:208px;text-align:center;color:var(--white);font-size:46px;font-weight:400;line-height:56px;text-shadow:0 1px 3px rgba(0,0,0,.35)}
.hero-sub{left:0;width:818px;top:265px;text-align:center;color:var(--white);font-size:10.5px}
.chev{top:258px}

/* welcome */
.welcome-title{left:0;width:818px;top:496px;text-align:center;font-size:24px;color:var(--blue);font-weight:400}
.welcome-copy{left:90px;width:638px;text-align:center;font-size:10.4px;line-height:16px;font-weight:300;color:var(--text)}

/* testimonials */
.band{left:0;top:697px;width:818px;height:292px;background:var(--grey-band)}
.band-title{left:0;width:818px;top:733px;text-align:center;font-size:20px;font-weight:300;color:var(--text-dark)}
.quote{left:160px;width:498px;top:788px;text-align:center;font-size:13.4px;line-height:19px;font-style:italic;font-weight:300;color:var(--text)}
.qmark{font-family:Georgia,serif;font-size:40px;color:#dddddd;line-height:40px;font-weight:700}
.avatar{left:367px;top:839px;width:86px;height:86px;border-radius:50%;background:var(--white);border:1px solid #dddddd}
.avatar-photo{left:373px;top:845px;width:74px;height:74px;border-radius:50%;background:radial-gradient(circle,#bdbdbd,#777777)}
.author{left:0;width:818px;top:928px;text-align:center;font-size:10px;letter-spacing:1px;color:var(--text-dark)}

/* footer */
.col-rule{top:1016px;width:1px;height:108px;background:var(--rule)}
.letter-label{left:68px;width:96px;top:1023px;text-align:center;font-size:7px;color:var(--blue-pale)}
.letter-thumb{left:84px;top:1037px;width:64px;height:84px;border:1px solid #999999;background:linear-gradient(180deg,#f6f6f6,#e9e9e9)}
.f-head{top:1020px;font-size:12.5px;color:var(--blue);font-weight:400}
.post-title{left:219px;top:1045px;font-size:8px;color:var(--text-dark)}
.post-date{left:219px;top:1058px;font-size:7.5px;color:#999999}
.post-excerpt{left:219px;top:1074px;width:178px;font-size:6.4px;line-height:10.4px;color:var(--text-dark)}
.post-more{left:219px;top:1105px;font-size:6.4px;color:var(--blue);text-decoration:underline}
.links{left:466px;top:1045px;list-style:none;font-size:8px;color:var(--text);line-height:19.2px}
.contact{left:650px;top:1045px;font-size:8px;line-height:13.6px;color:var(--text)}
.contact svg{vertical-align:-1px;margin-right:2px}

.bottom-bar{left:0;top:1160px;width:818px;height:40px;background:var(--blue-pale)}
.copyright{left:0;width:818px;top:1174px;text-align:center;font-size:8px;color:#555555}
</style>
</head>
<body>

<header>
  <div class="abs brand">
    <div class="brand-name">Halden Row Investment Company</div>
    <div class="brand-tag">Separately Managed Accounts</div>
  </div>
  <div class="abs header-rule"></div>
  <ul class="abs nav">
    <li class="active">HOME</li><li>PHILOSOPHY</li><li>PERFORMANCE</li><li>TEAM</li><li>LETTERS</li><li>COMMENTARY</li><li>CONTACT</li>
  </ul>
</header>

<section>
  <div class="abs hero" role="img" aria-label="Photograph of the historic white clapboard train station under a blue sky"></div>
  <div class="abs hero-shade"></div>
  <h1 class="abs hero-title">Halden Row Investment Company</h1>
  <p class="abs hero-sub">The high expectations of our original investors is a key contributor to our value driven investment philosophy.</p>
  <svg class="abs chev" style="left:23px" width="12" height="26" viewBox="0 0 12 26"><path d="M11 1 1 13l10 12" fill="none" stroke="#fff" stroke-width="1" opacity=".8"/></svg>
  <svg class="abs chev" style="left:776px" width="12" height="26" viewBox="0 0 12 26"><path d="M1 1l10 12L1 25" fill="none" stroke="#fff" stroke-width="1" opacity=".8"/></svg>
</section>

<section>
  <h2 class="abs welcome-title">Welcome to Halden Row Investment Company</h2>
  <p class="abs welcome-copy" style="top:545px">We founded Halden Row Investment Company in 1999, initially managing wealth from our family and friends in the town of Halden Row. The high expectations of our original investors is a key contributor to our value driven investment philosophy.</p>
  <p class="abs welcome-copy" style="top:597px">Based in Dallas, TX, we manage assets for both individuals and institutions. Our investment methodology stresses absolute returns vs. relative performance, blending a combination of fundamental analysis, discipline and patience with the goal of preserving and compounding capital.</p>
</section>

<section>
  <div class="abs band"></div>
  <h3 class="abs band-title">Clients Testimonials</h3>
  <div class="abs qmark" style="left:138px;top:778px">&ldquo;</div>
  <div class="abs qmark" style="left:646px;top:804px">&rdquo;</div>
  <p class="abs quote">"The stock market is filled with individuals who know the price of everything, but the value of nothing."</p>
  <svg class="abs" style="left:68px;top:800px" width="12" height="26" viewBox="0 0 12 26"><path d="M11 1 1 13l10 12" fill="none" stroke="#bbb" stroke-width="1"/></svg>
  <svg class="abs" style="left:738px;top:800px" width="12" height="26" viewBox="0 0 12 26"><path d="M1 1l10 12L1 25" fill="none" stroke="#bbb" stroke-width="1"/></svg>
  <div class="abs avatar"></div>
  <div class="abs avatar-photo" role="img" aria-label="Portrait photo of the quoted author"></div>
  <div class="abs author">– WALTER BRENNING</div>
</section>

<footer>
  <div class="abs letter-label">Investment Adviser's Letter</div>
  <div class="abs letter-thumb" role="img" aria-label="Cover of the quarterly investment adviser's letter"></div>
  <div class="abs col-rule" style="left:197px"></div>
  <div class="abs col-rule" style="left:425px"></div>
  <div class="abs col-rule" style="left:607px"></div>

  <h4 class="abs f-head" style="left:219px">LATEST COMMENTARY</h4>
  <div class="abs post-title">Core Equity Portfolio – Q2 2017</div>
  <div class="abs post-date">August 10, 2017</div>
  <p class="abs post-excerpt">Based on our estimate of fair value relative to the company's current stock price, we determine each company's current margin of safety in the Core Equity ...</p>
  <div class="abs post-more">CONTINUE READING</div>

  <h4 class="abs f-head" style="left:467px">QUICK LINKS</h4>
  <ul class="abs links">
    <li>› Performance Overview</li>
    <li>› Performance Analysis</li>
    <li>› Verification Statement</li>
    <li>› Halden Row ADV Part 2</li>
  </ul>

  <h4 class="abs f-head" style="left:650px">CONTACT US</h4>
  <div class="abs contact">
    <div><svg width="6" height="8" viewBox="0 0 6 8"><path d="M3 0a3 3 0 0 0-3 3c0 2 3 5 3 5s3-3 3-5a3 3 0 0 0-3-3z" fill="#555"/><circle cx="3" cy="3" r="1" fill="#fff"/></svg>1250 Cedar Park Avenue,</div>
    <div>Suite 900</div>
    <div>Dallas, TX 75201</div>
    <div style="margin-top:3px"><svg width="8" height="8" viewBox="0 0 8 8"><path d="M1 0h2l1 2-1 1c.5 1 1 1.5 2 2l1-1 2 1v2c0 .5-.5 1-1 1C3 8 0 5 0 1c0-.5.5-1 1-1z" fill="#555"/></svg>555.014.7732</div>
    <div><svg width="9" height="7" viewBox="0 0 9 7"><rect x=".5" y=".5" width="8" height="6" fill="none" stroke="#555"/><path d="M.5.5l4 3 4-3" fill="none" stroke="#555"/></svg>info@qlvor.example</div>
  </div>

  <div class="abs bottom-bar"></div>
  <div class="abs copyright">Copyrights © 2017 Halden Row Investment Company. All Rights Reserved.</div>
</footer>

</body>
</html>
```